Bright and beautiful business card for a coach

I'm a personal and business coach based in Perth, Australia. I need a business card that whilst subtle and elegant, will stand out and appeal on a table full of cards.

My business name is Fern Mentoring and the business card must represent the warmth and brightness implied in the name, without being gimmicky. It must have a warmth and appeal and be easy to read.

I prefer clean, minimalist designs.

It must align with the feel of my website and socials: https://www.fernmentoring-example.com.au/
https://www.instagram.com/fernmentoringau/
https://www.facebook.com/fernmentoringau
Updates

Hi Designers Thank you so much for taking the time to submit designs. I wonder if I could have explained myself a little better. Most of the designs that have been submitted look rather formal and many have quite corporate looking embellishments on them (to my eye). I would like softer, warmer, more organic. I’m open to people playing about and being more abstract, using softer embellishments (e.g the line drawing flowers and grasses I’ve used in my socials) incorporating other colours from my palette or like the social icons in my email signature (in PDF), perhaps playing with size/oversize, playing with the bleed. Please don’t be constrained by what I’ve already done, it merely needs to compliment. I’m sorry if I’m not using the right words or have led you astray. I’m no designer, but I’ve done my website, socials, email signature etc all myself (my logo was a design contest) and I was really hoping for my business card to be something more creative than I could have made with a template. Reminder: No black cards/sides please. Thank you 😊

Target Market(s)

Individuals, most likely but not all female. Creative thinkers. Likely professionals.

Industry/Entity Type

Business & Personal Coach

Contact Information for Business Card

(Fern Mentoring Logo) Name: Greta Pellham; Title: Business & Personal Coach; Phone number: +61 (0)458 913307; Email: greta@fernmentoring-example.com.au; Website: https://fernmentoring-example.com.au; Social icons for Facebook, Instagram & LinkedIn: @fernmentoringAU. Optional strapline: "A calm guide to help you find your way forward"

Font styles to use
Sans Serif

Colors
00AB8E
00BBA5
67D7C9
C6EFE9
E9F9F6
59FF00
82FF00
B8FF75
E3FFCB
F4FFEA
FFC000
F8CF3A
FAE287
FDF2CF
FEFAEE

Requirements
Must have
• Must align with feel of my website and socials. Must have a pop of #FFC000 (possibly whole of one side, or at least a block). Bright or white background. Easy to read.
Nice to have
• Possibly incorporate the sunshine/grass picture I have used in website and socials - will upload.
Should not have
• Must not be black or dark. Not impersonal or corporate looking.

```html
<!DOCTYPE html>
<html lang="en">
<head>
<meta charset="utf-8">
<title>Fern Mentoring – Business Card</title>
<link rel="stylesheet" href="https://fonts.googleapis.com/css2?family=Montserrat:wght@400;500;700;800&family=Roboto:wght@400;500&display=swap">
<style>
  :root {
    --stage: #d8d8d8;
    --paper: #ffffff;
    --amber: #c8782a;
    --amber-deep: #b45f22;
    --gold: #e9b62a;
    --gold-line: #e2a93a;
    --ink-grey: #5a5a5a;
    --pill-grey: #9a9a9a;
    --white: #ffffff;
  }
  * { box-sizing: border-box; margin: 0; padding: 0; }
  html, body {
    width: 1200px; height: 788px; overflow: hidden;
    background: var(--stage);
  }
  .stage {
    width: 1200px; height: 788px;
    display: flex; align-items: center; justify-content: center; gap: 40px;
  }
  .card {
    position: relative;
    width: 540px; height: 330px;
    border-radius: 22px;
    overflow: hidden;
    box-shadow: 0 10px 28px rgba(0,0,0,.18);
  }

  /* Front */
  .card--front { background: var(--paper); }
  .brand-mark {
    position: absolute; left: 28px; top: 150px;
    display: flex; align-items: center; gap: 10px;
  }
  .brand-mark__dot {
    width: 14px; height: 14px; border-radius: 50%;
    background: var(--amber);
  }
  .brand-mark__name {
    font-family: 'Montserrat', sans-serif;
    font-weight: 500; font-size: 24px; letter-spacing: 1px;
    color: var(--amber);
  }
  .divider {
    position: absolute; left: 270px; top: 70px;
    width: 1px; height: 150px; background: var(--gold-line);
  }
  .contact {
    position: absolute; left: 288px; top: 58px; right: 14px;
  }
  .contact__name {
    font-family: 'Montserrat', sans-serif;
    font-weight: 800; font-size: 24px; letter-spacing: .5px;
    color: var(--amber-deep); text-transform: uppercase;
    line-height: 1;
  }
  .contact__title {
    font-family: 'Roboto', sans-serif;
    font-size: 13px; color: var(--ink-grey);
    margin-top: 5px; margin-bottom: 12px;
  }
  .contact__list { list-style: none; }
  .contact__item {
    display: flex; align-items: center; gap: 6px;
    font-family: 'Roboto', sans-serif; font-size: 12.5px;
    color: var(--ink-grey); line-height: 20px; white-space: nowrap;
  }
  .contact__icon { width: 12px; height: 12px; flex: none; fill: var(--amber); }
  .social-dots { display: flex; gap: 3px; }
  .social-dots span {
    width: 12px; height: 12px; border-radius: 50%; background: var(--amber);
  }
  .edge-band {
    position: absolute; left: 0; right: 0; bottom: 0; height: 12px;
    background: linear-gradient(90deg, var(--amber-deep), var(--gold));
  }
  .strapline {
    position: absolute; right: 18px; bottom: 12px;
    width: 350px; height: 30px;
    border-radius: 15px 15px 0 0;
    background: var(--pill-grey);
    display: flex; align-items: center; justify-content: center;
    font-family: 'Roboto', sans-serif; font-size: 12px; color: var(--white);
    white-space: nowrap;
  }

  /* Back */
  .card--back {
    background:
      linear-gradient(200deg, rgba(255,255,255,.08) 0 30%, rgba(255,255,255,0) 30% 100%),
      linear-gradient(20deg, var(--amber-deep) 0%, var(--amber) 50%, var(--gold) 100%);
    display: flex; align-items: center; justify-content: center;
  }
  .brand-mark--back {
    position: static; gap: 14px;
  }
  .brand-mark--back .brand-mark__dot {
    width: 18px; height: 18px; background: var(--white);
  }
  .brand-mark--back .brand-mark__name {
    font-size: 36px; letter-spacing: 2px; color: var(--white);
  }
</style>
</head>
<body>
<main class="stage">

  <section class="card card--front" aria-label="Card front">
    <div class="brand-mark">
      <span class="brand-mark__dot"></span>
      <span class="brand-mark__name">Fern Mentoring</span>
    </div>

    <div class="divider"></div>

    <div class="contact">
      <h1 class="contact__name">Greta Pellham</h1>
      <p class="contact__title">Business &amp; Personal Coach</p>
      <ul class="contact__list">
        <li class="contact__item">
          <svg class="contact__icon" viewBox="0 0 24 24"><path d="M6.6 10.8a15 15 0 0 0 6.6 6.6l2.2-2.2a1 1 0 0 1 1-.25 11.4 11.4 0 0 0 3.6.57 1 1 0 0 1 1 1V20a1 1 0 0 1-1 1A17 17 0 0 1 3 4a1 1 0 0 1 1-1h3.5a1 1 0 0 1 1 1 11.4 11.4 0 0 0 .57 3.6 1 1 0 0 1-.25 1z"/></svg>
          +61 (0)458 913307
        </li>
        <li class="contact__item">
          <svg class="contact__icon" viewBox="0 0 24 24"><path d="M2 5h20v14H2z M2 5l10 8 10-8" fill="none" stroke="#c8782a" stroke-width="2.4"/></svg>
          greta@fernmentoring-example.com.au
        </li>
        <li class="contact__item">
          <svg class="contact__icon" viewBox="0 0 24 24"><circle cx="12" cy="12" r="10" fill="none" stroke="#c8782a" stroke-width="2.4"/><path d="M2 12h20M12 2c3 3 3 17 0 20M12 2c-3 3-3 17 0 20" fill="none" stroke="#c8782a" stroke-width="2"/></svg>
          www.fernmentoring-example.com.au
        </li>
        <li class="contact__item">
          <span class="social-dots" aria-hidden="true"><span></span><span></span><span></span></span>
          @fernmentoringAU
        </li>
      </ul>
    </div>

    <p class="strapline">A calm guide to help you find your way forward</p>
    <div class="edge-band"></div>
  </section>

  <section class="card card--back" aria-label="Card back">
    <div class="brand-mark brand-mark--back">
      <span class="brand-mark__dot"></span>
      <span class="brand-mark__name">Fern Mentoring</span>
    </div>
  </section>

</main>
</body>
</html>
```